KDN Roofing Truck and Trailer Wrap

I need a graphic wrap on my Toyota Tundra pickup truck, and our 14' enclosed trailer

Target Market(s)

Home Owners

Industry/Entity Type

Roofing

Requirements
Must have
• Harwell Siding Supply and TBR Logos
Nice to have
• Our services listed somewhere on the truck, maybe on the back tailgate and also on the sides at the very bottom of the doors: Roofing, Siding, Gutters, Painting

```html
<!DOCTYPE html>
<html lang="en">
<head>
<meta charset="utf-8">
<title>KDN Roofing – Trailer Wrap</title>
<link href="https://fonts.googleapis.com/css2?family=Poppins:wght@500;600&display=swap" rel="stylesheet">
<style>
  :root{
    --ink:#0b0b0b;
    --paper:#ffffff;
    --gold:#d18a2c;
    --gold-light:#f0c050;
    --gold-deep:#b86a1c;
    --stage:#e4e5e7;
    --cutout:#c9ccd1;
  }
  *{margin:0;padding:0;box-sizing:border-box}
  html,body{width:784px;height:1200px;overflow:hidden;background:var(--stage)}
  .canvas{position:relative;width:784px;height:1200px;font-family:"Poppins",sans-serif}
  .wrap{position:absolute;overflow:hidden;background:var(--ink)}
  .wrap svg.shapes{position:absolute;inset:0}
  .abs{position:absolute;white-space:nowrap}
  .brand-name{font-weight:600;color:var(--ink);line-height:1;letter-spacing:-0.5px}
  .phone{font-weight:600;color:var(--gold);line-height:1}
  .services{font-weight:600;color:var(--ink);line-height:1}
  .web{font-weight:600;line-height:1}
  .partner{font-weight:600;color:var(--paper);line-height:1.1}
  .partner-big{font-weight:600;color:var(--paper);font-size:24px;line-height:1}
  .bullets{list-style:none;color:var(--paper);font-weight:600;font-size:18px;line-height:23px}
  .bullets li::before{content:"• ";font-size:13px}
  .center{transform:translateX(-50%);text-align:center}
  .front-panel{position:absolute;background:var(--paper);width:102px;height:177px;top:938px}
</style>
</head>
<body>
<div class="canvas">

  <!-- Curb side -->
  <section class="wrap" style="left:165px;top:70px;width:580px;height:262px">
    <svg class="shapes" width="580" height="262" viewBox="0 0 580 262">
      <defs>
        <linearGradient id="goldA" x1="0" y1="0" x2="1" y2="1">
          <stop offset="0" stop-color="var(--gold-deep)"/>
          <stop offset=".5" stop-color="var(--gold)"/>
          <stop offset="1" stop-color="var(--gold-light)"/>
        </linearGradient>
      </defs>
      <polygon points="0,0 520,0 405,176 0,176" fill="var(--paper)"/>
      <polygon points="520,0 551,0 431,180 405,180" fill="url(#goldA)"/>
      <rect x="0" y="176" width="420" height="4" fill="url(#goldA)"/>
      <path d="M201,262 L201,228 Q205,190 260,188 L410,188 Q466,190 470,228 L470,262 Z" fill="var(--cutout)"/>
    </svg>
    <div class="abs brand-name" style="left:20px;top:34px;font-size:46px">KDN Roofing</div>
    <div class="abs phone" style="left:44px;top:104px;font-size:27px">317-555-0142</div>
    <div class="abs services" style="left:30px;top:146px;font-size:19px">Roofing - Siding - Gutters - Painting</div>
    <div class="abs web" style="left:18px;top:208px;font-size:20px;color:var(--gold)">kdnroofing.com</div>
    <div class="abs partner" style="left:478px;top:168px;font-size:10px;width:90px;white-space:normal;text-align:center">Harwell Siding Supply</div>
    <div class="abs partner-big" style="left:505px;top:205px">TBR</div>
  </section>

  <!-- Road side -->
  <section class="wrap" style="left:52px;top:538px;width:565px;height:262px">
    <svg class="shapes" width="565" height="262" viewBox="0 0 565 262">
      <defs>
        <linearGradient id="goldB" x1="0" y1="0" x2="1" y2="1">
          <stop offset="0" stop-color="var(--gold-deep)"/>
          <stop offset=".5" stop-color="var(--gold)"/>
          <stop offset="1" stop-color="var(--gold-light)"/>
        </linearGradient>
      </defs>
      <polygon points="50,0 565,0 565,176 173,176" fill="var(--paper)"/>
      <polygon points="18,0 50,0 173,180 146,180" fill="url(#goldB)"/>
      <rect x="160" y="176" width="405" height="4" fill="url(#goldB)"/>
      <path d="M112,262 L114,236 Q124,190 172,188 L306,188 Q362,190 366,228 L366,262 Z" fill="var(--cutout)"/>
    </svg>
    <div class="abs brand-name center" style="left:270px;top:32px;font-size:46px">KDN Roofing</div>
    <div class="abs phone center" style="left:263px;top:104px;font-size:28px">317-555-0142</div>
    <div class="abs web center" style="left:263px;top:142px;font-size:19px;color:var(--ink)">kdnroofing.com</div>
    <ul class="abs bullets" style="left:16px;top:128px">
      <li>Roofing</li><li>Siding</li><li>Gutter</li><li>Painting</li>
    </ul>
    <div class="abs partner" style="left:390px;top:200px;font-size:10px;width:70px;white-space:normal;text-align:center">Harwell Siding Supply</div>
    <div class="abs partner-big" style="left:478px;top:206px">TBR</div>
  </section>

  <!-- Rear doors -->
  <section class="wrap" style="left:119px;top:961px;width:197px;height:194px">
    <svg class="shapes" width="197" height="194" viewBox="0 0 197 194">
      <defs>
        <linearGradient id="goldC" x1="0" y1="0" x2="1" y2="0">
          <stop offset="0" stop-color="var(--gold-deep)"/>
          <stop offset=".5" stop-color="var(--gold-light)"/>
          <stop offset="1" stop-color="var(--gold)"/>
        </linearGradient>
      </defs>
      <polygon points="30,167 183,167 195,194 18,194" fill="url(#goldC)"/>
    </svg>
    <div class="abs brand-name center" style="left:98px;top:74px;font-size:24px;color:var(--paper)">KDN Roofing</div>
    <div class="abs phone center" style="left:98px;top:112px;font-size:17px">317-555-0142</div>
    <div class="abs services center" style="left:98px;top:144px;font-size:9.5px;color:var(--paper)">Roofing - Siding - Gutters - Painting</div>
    <div class="abs web center" style="left:99px;top:173px;font-size:14px;color:var(--ink)">kdnroofing.com</div>
  </section>

  <!-- Front nose -->
  <section class="front-panel" style="left:514px">
    <div class="abs brand-name center" style="left:51px;top:96px;font-size:13px">KDN Roofing</div>
  </section>
  <section class="front-panel" style="left:628px">
    <div class="abs brand-name center" style="left:51px;top:96px;font-size:13px">KDN Roofing</div>
  </section>

</div>
</body>
</html>
```